German Headhunter/ HR Consultancy needs Business Cards Design

We need a business Card Design for our Company in Stuttgart. We are specialized as Headhunter/ HR Consultancy in Placement of specialist and managers in permanent employment. Please refer to our business logo.

```html
<!DOCTYPE html>
<html lang="en">
<head>
<meta charset="utf-8">
<title>Lindenhof Personalberatung – Business Cards</title>
<link href="https://fonts.googleapis.com/css2?family=Karla:wght@400;500;700&display=swap" rel="stylesheet">
<style>
  :root {
    --page-bg: #e6e6e6;
    --card-white: #f6f6f6;
    --brand-blue: #3f55a8;
    --blue-light: #6a7bc6;
    --blue-dark: #32479b;
    --stripe-grey: #8a8a8e;
    --text-grey: #6d6d70;
    --back-light: #77777b;
    --back-dark: #58585c;
    --ink-dark: #2a2a2c;
    --on-dark: #f2f2f4;
  }
  * { margin: 0; padding: 0; box-sizing: border-box; }
  html, body { width: 1200px; height: 1200px; overflow: hidden; }
  body {
    background: var(--page-bg);
    font-family: "Karla", Arial, sans-serif;
    position: relative;
  }
  .card {
    position: absolute;
    left: 262px;
    width: 686px;
    height: 392px;
    border-radius: 20px;
    overflow: hidden;
  }
  .card--front { top: 165px; background: var(--card-white); }
  .card--back {
    top: 653px;
    background: linear-gradient(180deg, var(--back-light) 0%, var(--back-dark) 100%);
  }
  .card__shapes { position: absolute; inset: 0; }

  .wordmark {
    position: absolute;
    display: flex;
    align-items: center;
    gap: 14px;
    font-weight: 700;
    line-height: 1;
  }
  .wordmark__square { width: 14px; height: 14px; }
  .wordmark__lines { display: flex; flex-direction: column; gap: 5px; }

  .front-wordmark { left: 46px; top: 66px; color: var(--brand-blue); }
  .front-wordmark .wordmark__square { background: var(--brand-blue); }
  .front-wordmark .wordmark__name { font-size: 32px; letter-spacing: 0.5px; }
  .front-wordmark .wordmark__sub { font-size: 14.5px; letter-spacing: 0.6px; }

  .contact {
    position: absolute;
    right: 40px;
    top: 153px;
    text-align: right;
    color: var(--on-dark);
  }
  .contact__name { font-size: 21px; font-weight: 700; letter-spacing: 0.6px; line-height: 1.1; }
  .contact__role { font-size: 14px; letter-spacing: 0.5px; margin-top: 2px; }
  .contact__address { font-size: 14px; letter-spacing: 0.4px; line-height: 19px; margin-top: 12px; }
  .contact__list { list-style: none; margin-top: 10px; font-size: 14px; letter-spacing: 0.4px; }
  .contact__item { display: flex; justify-content: flex-end; align-items: center; gap: 9px; height: 19.5px; }
  .contact__icon { width: 13px; height: 13px; fill: var(--on-dark); }

  .back-wordmark {
    left: 50%;
    top: 152px;
    transform: translateX(-50%);
    color: var(--ink-dark);
    gap: 18px;
  }
  .back-wordmark .wordmark__square { background: var(--on-dark); width: 20px; height: 20px; }
  .back-wordmark .wordmark__name { font-size: 48px; letter-spacing: 1px; }
  .back-wordmark .wordmark__sub { font-size: 21.5px; letter-spacing: 0.8px; }

  .tagline {
    position: absolute;
    left: 0; right: 0;
    top: 315px;
    text-align: center;
    color: var(--on-dark);
    font-size: 14.5px;
    letter-spacing: 0.4px;
    line-height: 19px;
  }
</style>
</head>
<body>

<section class="card card--front">
  <svg class="card__shapes" viewBox="0 0 686 392" width="686" height="392" aria-hidden="true">
    <defs>
      <linearGradient id="blueField" x1="0" y1="0" x2="0" y2="1">
        <stop offset="0" stop-color="#6a7bc6"/>
        <stop offset="1" stop-color="#32479b"/>
      </linearGradient>
    </defs>
    <polygon points="557,0 566,0 160,392 150,392" fill="var(--stripe-grey)"/>
    <polygon points="571,0 686,0 686,392 166,392" fill="url(#blueField)"/>
  </svg>

  <div class="wordmark front-wordmark">
    <span class="wordmark__square"></span>
    <div class="wordmark__lines">
      <span class="wordmark__name">LINDENHOF</span>
      <span class="wordmark__sub">PERSONALBERATUNG</span>
    </div>
  </div>

  <div class="contact">
    <div class="contact__name">MARTIN KELLER</div>
    <div class="contact__role">Founder &amp; CEO</div>
    <div class="contact__address">1420 Birchwood Avenue<br>Fairview, Oregon 50218</div>
    <ul class="contact__list">
      <li class="contact__item">555-210-4837
        <svg class="contact__icon" viewBox="0 0 16 16"><path d="M3.6 1.2l2.3 2.6-1.3 1.7c.9 2 2.8 3.9 4.9 4.9l1.7-1.3 2.6 2.3-1.3 2.2C7.3 13.3 2.7 8.7 1.4 2.5z"/></svg>
      </li>
      <li class="contact__item">555-392-6104
        <svg class="contact__icon" viewBox="0 0 16 16"><path d="M4 0h8a1 1 0 0 1 1 1v14a1 1 0 0 1-1 1H4a1 1 0 0 1-1-1V1a1 1 0 0 1 1-1zm1 2v11h6V2z"/></svg>
      </li>
      <li class="contact__item">555-718-2950
        <svg class="contact__icon" viewBox="0 0 16 16"><path d="M4 1h6l2 2v3H4zM1 7h14v6h-2v-2H3v2H1zm3 5h8v3H4z"/></svg>
      </li>
      <li class="contact__item">martin@lindenhof.example
        <svg class="contact__icon" viewBox="0 0 16 16"><path d="M1 3h14v10H1zm1.5 1.2L8 8.3l5.5-4.1z"/></svg>
      </li>
      <li class="contact__item">www.lindenhof.example
        <svg class="contact__icon" viewBox="0 0 16 16"><path d="M8 1a7 7 0 1 0 0 14A7 7 0 0 0 8 1zm-1 2.2c-.6 1-.3 2 .6 2.4.8.4.4 1.5-.4 1.8-1 .4-1.2 1.6-.4 2.4.6.6.4 1.7-.2 2.6A5 5 0 0 1 7 3.2zm3 1.1c1.6.9 2.6 2.8 2.2 4.7-.8-.4-1.3-1.3-2-1.5-.8-.2-1.4-1.2-.8-1.8.5-.5.8-1 .6-1.4z"/></svg>
      </li>
    </ul>
  </div>
</section>

<section class="card card--back">
  <div class="wordmark back-wordmark">
    <span class="wordmark__square"></span>
    <div class="wordmark__lines">
      <span class="wordmark__name">LINDENHOF</span>
      <span class="wordmark__sub">PERSONALBERATUNG</span>
    </div>
  </div>
  <p class="tagline">We are specialized as Headhunter/ HR Consultancy in Placement of<br>specialist and managers in permanent employment.</p>
</section>

</body>
</html>
```